Modern & Simple Essential Oils Label

Company Name: Meadowlark Essentials

What we sell: Aromatherapy products, pure therapeutic essential oils.

Design need:
We are looking for a creative and youthful design for the labels used on small essentials oils.

I have two sizes of bottles that I use for essential oils a 5ml bottle and a 15ml bottle. They are dark Amber color glass with black lids. I like the clear labels or mayble a dark brown background. With white or clear lettering with punch of color too! Each oil type is represented by different color. (lavender- purple, lemon - yellow). The label will be the same for all the oils in the two sizes with only a different oil name & coordinating color.
5ml label size should be: 1 " x 2.625"
15ml label size should be: 1.5" x 3.5"

I have some labels that I have had another designer start on, but they aren't quite what I want and missing that something (alot!).. I don't know what. Interest maybe? Lack of design? I dunno.. they are attached. Maybe it's the logo? I don't know! But its gotta change! When I cut out a proof and put a sample on the bottle as I look straight on at the label all I see is a big dot, no logo.. nothing interesting.
Updates

Project Deadline Extended
Reason: Hi! Id like to extend this deadline. Ive been unavailable for a few days due to an illness and Im so far behind! Im feeling MUCH better and looking forward to getting caught up and move with the project. Im not sure how this works, but I attached a list of the oils that we currently have available. And in the list is the idea for the color schemes for the oils. The basic idea is for it to have a wide array of colors, so using different shades of greens, yellows, oranges and so on. So that its like a rainbow. We are not set of that particular color for that particular oil. It was just a idea list of possible colors for oils. Thanks so much!

Target Market(s)

Metro & Modern people. Interested in healthy organic living, Mostly women (some men) 20-45 who are interested in holistic healing.

Industry/Entity Type

It Company

Requirements
Must have
• A reputable look. Clean, organic, crisp, zen or spa-like feel. Modern, youthful appealing label design. Approachable and interesting, not intimidating so that I don't turn away people who are new or not familiar with how to use essential oils.
Should not have
• do NOT want the look to be anywhere close to medicinal, witchy, crafty, hippie, mystical, overly earthy, magical, or voodoo. Do not want it to look like something out of a grandmothers medicine cabinet.

```html
<!DOCTYPE html>
<html lang="en">
<head>
<meta charset="utf-8">
<title>Meadowlark Essentials – Rosemary 15 ml Label</title>
<link rel="stylesheet" href="https://fonts.googleapis.com/css2?family=Raleway:wght@400&family=Open+Sans:wght@600&family=Dancing+Script:wght@500&display=swap">
<style>
  :root {
    --backdrop: #e6e6e6;
    --label-paper: #f6f4f5;
    --label-stripe: rgba(200, 190, 196, 0.35);
    --accent-circle: #eddde3;
    --illustration-tone: #b58aa3;
    --oil-name: #5a2146;
    --brand: #8e3f8f;
    --volume: #2b1a22;
  }

  * { margin: 0; padding: 0; box-sizing: border-box; }

  html, body {
    width: 1200px;
    height: 834px;
    overflow: hidden;
  }

  body {
    background: var(--backdrop);
    position: relative;
  }

  .label {
    position: absolute;
    left: 447px;
    top: 235px;
    width: 306px;
    height: 364px;
    background-color: var(--label-paper);
    background-image: repeating-linear-gradient(
      90deg,
      transparent 0,
      transparent 9px,
      var(--label-stripe) 9px,
      var(--label-stripe) 10px
    );
    box-shadow: 0 1px 3px rgba(0, 0, 0, 0.08);
  }

  .label__circle {
    position: absolute;
    left: 33px;
    top: 28px;
    width: 236px;
    height: 236px;
    border-radius: 50%;
    background: var(--accent-circle);
  }

  .label__illustration {
    position: absolute;
    left: 100px;
    top: 58px;
    width: 62px;
    height: 218px;
    border-radius: 20px 20px 4px 4px;
    background: linear-gradient(180deg, rgba(181, 138, 163, 0.55), rgba(181, 138, 163, 0.35));
  }

  .label__oil-name {
    position: absolute;
    left: 152px;
    top: 132px;
    font-family: "Dancing Script", cursive;
    font-weight: 500;
    font-size: 34px;
    line-height: 1;
    color: var(--oil-name);
    transform: rotate(-4deg);
    transform-origin: left center;
  }

  .label__brand {
    position: absolute;
    left: 0;
    right: 0;
    top: 292px;
    text-align: center;
    font-family: "Raleway", sans-serif;
    font-weight: 400;
    font-size: 23px;
    line-height: 1;
    color: var(--brand);
    white-space: nowrap;
  }

  .label__volume {
    position: absolute;
    left: 0;
    right: 0;
    top: 331px;
    text-align: center;
    font-family: "Open Sans", sans-serif;
    font-weight: 600;
    font-size: 17px;
    line-height: 1;
    color: var(--volume);
  }
</style>
</head>
<body>
  <main class="label">
    <div class="label__circle"></div>
    <div class="label__illustration" role="img" aria-label="Line drawing of three long-stemmed roses with leaves"></div>
    <p class="label__oil-name">Rosemary</p>
    <p class="label__brand">Meadowlark Essentials</p>
    <p class="label__volume">15 ml</p>
  </main>
</body>
</html>
```